Business Cards for new orthopaedic surgery practice

My husband and I are starting our own orthopaedic surgery practice. We are looking for a business card that is uniform, but one will have my name/title and the other will have his. You can just create one design with my name on it for now. But when I choose your design as the winning design I will ask that you add another copy with his name/title.

We are looking for classy, simple, elite all in one. We like dark blues/a little gold/yellow. Something that goes with our logo. We want our logo incorporated. Here is all the info you need:
Business name: RV Bone & Vitality Center
Location: 38517 North Willowmere Ave
Maple Hollow, FL 33990
Phone: 954-218-4063
Fax: 954-582-7341
Email: info@myrvbonecare.example

Names: Lydia Vance, M.D.
Board Certified Hand and Upper Extremity Surgeon

Ebo Dansu, M.D.
Board Certified Hip & Knee Replacement/General Orthopaedic Surgeon

Can decide what you want to put on the back. Maybe a slogan:
Grounded in Care. Built for You

I am just going to upload our logo. The only thing is if we select you as the winning design, the location, and phone numbers may change. We will need your help to update that once fully solidified.

Industry/Entity Type

Medical

Contact Information for Business Card

Colors
0054AA
0677BA
7BADD7
CADEEF
E8F1F8
0094D4
00A9DD
6FCCEA
C7EBF8
E9F6FB

Requirements
Must have
• class, appeal,
Should not have
• We want to air on the side of masculine if we are looking at masculine vs. feminine feel. But we still want it classy, sophisticated, and something we will love

```html
<!DOCTYPE html>
<html lang="en">
<head>
<meta charset="utf-8">
<title>RV Bone &amp; Vitality Center – Business Card</title>
<link rel="stylesheet" href="https://fonts.googleapis.com/css2?family=Tinos:wght@700&family=Figtree:wght@400;500&display=swap">
<style>
  :root {
    --backdrop: #1b1b1d;
    --paper: #f4f4f3;
    --navy: #1c2b55;
    --navy-soft: #2c3d6e;
    --gold: #c49a55;
    --ink: #333640;
    --white: #ffffff;
  }
  * { margin: 0; padding: 0; box-sizing: border-box; }
  html, body { width: 1200px; height: 1059px; overflow: hidden; background: var(--backdrop); }
  .canvas { position: relative; width: 1200px; height: 1059px; }

  .card {
    position: absolute;
    width: 687px;
    height: 390px;
    border-radius: 18px;
    overflow: hidden;
  }
  .card--front { left: 257px; top: 89px; background: var(--paper); }
  .card--back { left: 254px; top: 547px; width: 693px; height: 393px; background: var(--navy); }

  .brand {
    position: absolute;
    display: flex;
    align-items: center;
    justify-content: center;
    text-align: center;
    border-radius: 50%;
    font-family: "Tinos", serif;
    font-weight: 700;
    letter-spacing: 0.04em;
    line-height: 1.25;
  }
  .brand--front {
    left: 278px; top: 46px; width: 130px; height: 130px;
    border: 1.5px solid var(--gold);
    color: var(--navy);
    font-size: 16px;
  }
  .brand--back {
    left: 243px; top: 73px; width: 206px; height: 206px;
    border: 2px solid var(--navy-soft);
    color: #33467c;
    font-size: 24px;
  }

  .identity {
    position: absolute;
    right: 365px;
    top: 216px;
    text-align: right;
  }
  .identity__name {
    font-family: "Tinos", serif;
    font-weight: 700;
    font-size: 25.5px;
    color: var(--navy);
    letter-spacing: 0.01em;
    line-height: 1;
    white-space: nowrap;
  }
  .identity__credential { color: var(--gold); }
  .identity__title {
    margin-top: 7px;
    font-family: "Figtree", sans-serif;
    font-size: 17.5px;
    color: var(--ink);
    line-height: 1.3;
    white-space: nowrap;
  }

  .divider {
    position: absolute;
    left: 343px; top: 216px;
    width: 1.5px; height: 72px;
    background: var(--gold);
  }

  .contacts {
    position: absolute;
    left: 362px; top: 210px;
    list-style: none;
    font-family: "Figtree", sans-serif;
    font-size: 17px;
    color: var(--ink);
  }
  .contacts__item { display: flex; align-items: center; height: 28px; white-space: nowrap; }
  .contacts__icon { width: 14px; height: 14px; margin-right: 8px; flex: none; }

  .band { position: absolute; left: 0; top: 293px; width: 687px; height: 97px; }

  .address {
    position: absolute;
    left: 0; right: 0; top: 355px;
    text-align: center;
    font-family: "Figtree", sans-serif;
    font-size: 17px;
    color: var(--white);
  }

  .slogan {
    position: absolute;
    left: 0; right: 0; top: 334px;
    text-align: center;
    font-family: "Figtree", sans-serif;
    font-weight: 500;
    font-size: 21px;
    color: var(--gold);
  }
</style>
</head>
<body>
<main class="canvas">

  <section class="card card--front" aria-label="Business card front">
    <div class="brand brand--front">RV Bone &amp;<br>Vitality<br>Center</div>

    <div class="identity">
      <p class="identity__name">LYDIA VANCE, <span class="identity__credential">M.D.</span></p>
      <p class="identity__title">Board Certified Hand and<br>Upper Extremity Surgeon</p>
    </div>

    <div class="divider"></div>

    <ul class="contacts">
      <li class="contacts__item">
        <svg class="contacts__icon" viewBox="0 0 24 24" aria-hidden="true"><path fill="#c49a55" d="M6.6 10.8a15.1 15.1 0 0 0 6.6 6.6l2.2-2.2c.3-.3.7-.4 1-.2 1.1.4 2.3.6 3.6.6.6 0 1 .4 1 1V20c0 .6-.4 1-1 1A17 17 0 0 1 3 4c0-.6.4-1 1-1h3.5c.6 0 1 .4 1 1 0 1.3.2 2.5.6 3.6.1.3 0 .7-.2 1z"/></svg>
        954-218-4063
      </li>
      <li class="contacts__item">
        <svg class="contacts__icon" viewBox="0 0 24 24" aria-hidden="true"><path fill="#c49a55" d="M6 2h12v6H6zM3 9h18a1 1 0 0 1 1 1v7h-4v5H6v-5H2v-7a1 1 0 0 1 1-1zm5 7v4h8v-4z"/></svg>
        954-582-7341
      </li>
      <li class="contacts__item">
        <svg class="contacts__icon" viewBox="0 0 24 24" aria-hidden="true"><path fill="#c49a55" d="M2 5h20v14H2zm2 2v.5l8 5.5 8-5.5V7l-8 5.3z"/></svg>
        info@myrvbonecare.example
      </li>
    </ul>

    <svg class="band" viewBox="0 0 687 97" aria-hidden="true">
      <path d="M0 0 Q343.5 90 687 0 V97 H0 Z" fill="#1c2b55"/>
      <path d="M25 4 Q343.5 82 662 4" fill="none" stroke="#c49a55" stroke-width="3"/>
    </svg>

    <p class="address">38517 North Willowmere Ave Maple Hollow, FL 33990</p>
  </section>

  <section class="card card--back" aria-label="Business card back">
    <div class="brand brand--back">RV Bone &amp;<br>Vitality<br>Center</div>
    <p class="slogan">Grounded in Care. Built for You</p>
  </section>

</main>
</body>
</html>
```